Velmora Consulting Business

** Please add the content information from my old business card
1. I would like to see a two sided business card with both options with the 1st Option--Tallow Spire-new WHITE BACKGROUND LOGO
2 nd Option-Tallow Spire - new BLACK- Background Logo
3rd -Option a business card with my Photo on the card
Please add the new word to the card information:
EXECUTION
AS THE OWNER'S REP
WE AIM TO ACHIEVE YOUR
INFRASTRUCTURE VISION with
OUR SPECIALIZATION & EXECUTION in:

FUNDING Planning
BUSINESS Planning
INFRASTRUCTURE Planning
PROJECT Management
Since 2012
_____________________________________________________________________
I want to get spot uv raised printing. I was liking a a nice rich white linen paper stock with black writing & NOT A COLORED CARD other than a variety of white or black cards concept

```html
<!DOCTYPE html>
<html lang="en">
<head>
<meta charset="utf-8">
<title>Velmora Consulting – Business Card</title>
<link rel="stylesheet" href="https://fonts.googleapis.com/css2?family=Roboto:wght@400;500;700&family=Roboto+Condensed:wght@700&display=swap">
<style>
  :root {
    --bg: #e4e4e6;
    --white: #ffffff;
    --ink: #231f20;
    --panel: #231f20;
    --red: #d7193a;
    --photo-a: #8a6a55;
    --photo-b: #2b2b2b;
  }
  * { box-sizing: border-box; margin: 0; padding: 0; }
  html, body { width: 1200px; height: 800px; overflow: hidden; }
  body {
    background: var(--bg);
    font-family: "Roboto", Arial, sans-serif;
    display: flex;
    align-items: center;
    justify-content: center;
    gap: 40px;
  }
  .card {
    position: relative;
    width: 560px;
    height: 320px;
    border-radius: 18px;
    overflow: hidden;
    box-shadow: 0 6px 18px rgba(0,0,0,.18);
  }

  /* ---------- front ---------- */
  .card--front { background: var(--white); }
  .front-art { position: absolute; inset: 0; }
  .brand {
    position: absolute;
    display: flex;
    align-items: center;
    gap: 10px;
    font-weight: 700;
  }
  .brand__dot {
    width: 14px; height: 14px; border-radius: 50%;
    background: var(--red);
    flex: none;
  }
  .brand__text { display: flex; flex-direction: column; line-height: 1; }
  .brand__name { font-size: 46px; letter-spacing: -1px; }
  .brand__sub { font-size: 11px; letter-spacing: 9px; margin-top: 6px; padding-left: 3px; }
  .card--front .brand { left: 28px; top: 130px; color: var(--ink); }
  .card--front .brand__name { font-size: 40px; }
  .card--front .brand__sub { font-size: 10px; letter-spacing: 7px; }

  .photo {
    position: absolute;
    left: 400px; top: 22px;
    width: 118px; height: 92px;
    border: 2px solid var(--red);
    border-radius: 8px;
    padding: 4px;
  }
  .photo__fill {
    width: 100%; height: 100%;
    border-radius: 4px;
    background: linear-gradient(135deg, var(--photo-a), var(--photo-b) 70%);
  }
  .contact {
    position: absolute;
    right: 30px; top: 128px;
    list-style: none;
    color: var(--white);
    font-size: 13px;
    text-align: right;
  }
  .contact li { display: flex; align-items: center; justify-content: flex-end; gap: 8px; height: 19px; }
  .contact svg { width: 12px; height: 12px; flex: none; }
  .locations {
    position: absolute; right: 30px; top: 200px;
    color: var(--white); font-size: 13px;
  }
  .locations .sep { color: var(--red); padding: 0 4px; }
  .person { position: absolute; right: 30px; top: 232px; text-align: right; }
  .person__name {
    font-family: "Roboto Condensed", "Arial Narrow", sans-serif;
    color: var(--red); font-size: 22px; line-height: 1.1;
  }
  .person__role { color: var(--white); font-size: 11px; letter-spacing: .3px; margin-top: 3px; }

  /* ---------- back ---------- */
  .card--back { background: var(--red); color: var(--white); }
  .pitch {
    position: absolute; left: 30px; top: 30px; width: 240px;
    font-size: 14px; line-height: 1.3;
  }
  .services {
    position: absolute; left: 30px; top: 168px;
    list-style: none; font-size: 15px; line-height: 1.3;
  }
  .services li { display: flex; align-items: center; gap: 10px; }
  .services li::before {
    content: ""; width: 7px; height: 7px; background: var(--white);
    transform: rotate(45deg); flex: none;
  }
  .services .since { padding-left: 17px; }
  .services .since::before { display: none; }
  .card--back .brand { right: 34px; top: 126px; color: var(--white); }
  .card--back .brand__dot { background: var(--white); }
</style>
</head>
<body>

  <section class="card card--front" aria-label="Business card, front">
    <svg class="front-art" viewBox="0 0 560 320" aria-hidden="true">
      <polygon points="262,0 560,0 560,320 300,320" fill="var(--panel)"/>
      <polygon points="244,0 254,0 292,320 282,320" fill="var(--red)"/>
      <polygon points="232,0 238,0 276,320 270,320" fill="var(--red)"/>
    </svg>

    <div class="brand">
      <span class="brand__dot"></span>
      <span class="brand__text">
        <span class="brand__name">Velmora</span>
        <span class="brand__sub">CONSULTING</span>
      </span>
    </div>

    <div class="photo"><div class="photo__fill" role="img" aria-label="Portrait photo of the card owner"></div></div>

    <ul class="contact">
      <li>555.201.4730
        <svg viewBox="0 0 12 12"><path d="M2 1h3l1 3-2 1a7 7 0 0 0 3 3l1-2 3 1v3c-6 0-10-4-10-9z" fill="var(--red)"/></svg></li>
      <li>marisol@velmora.ca
        <svg viewBox="0 0 12 12"><rect x="0.5" y="2" width="11" height="8" rx="1" fill="var(--red)"/><path d="M1 3l5 4 5-4" stroke="var(--panel)" fill="none"/></svg></li>
      <li>www.velmora.ca
        <svg viewBox="0 0 12 12"><circle cx="6" cy="6" r="5.5" fill="var(--red)"/><path d="M1 6h10M6 1c-3 3-3 7 0 10M6 1c3 3 3 7 0 10" stroke="var(--panel)" fill="none" stroke-width=".8"/></svg></li>
    </ul>

    <p class="locations">Harrowgate NT<span class="sep">•</span>Linden Falls NB</p>

    <div class="person">
      <h1 class="person__name">Marisol Pennington-Rhee</h1>
      <p class="person__role">CEO / LEAD PROJECT MANAGER</p>
    </div>
  </section>

  <section class="card card--back" aria-label="Business card, back">
    <p class="pitch">As the Owner's Rep we aim to achieve your Infrastructure vision with our Specialization &amp; Execution in</p>
    <ul class="services">
      <li>Funding Planning</li>
      <li>Business Planning</li>
      <li>Infrastructure Planning</li>
      <li>Project Management</li>
      <li class="since">Since 2012</li>
    </ul>
    <div class="brand">
      <span class="brand__dot"></span>
      <span class="brand__text">
        <span class="brand__name">Velmora</span>
        <span class="brand__sub">CONSULTING</span>
      </span>
    </div>
  </section>

</body>
</html>
```